Heron Loan Partners Business Card

We need a business card design for our mortgage servicing company. In addition to servicing the loans of homeowners, we help homeowners with purchasing their homes and any mortgage refinancing. We would like to see designs that use the colors in the logo attached below (gold-ish yellow and navy blue), and any other design you deem fit! The design should communicate a simpler life with smart mortgages provided by Heron.

```html
<!DOCTYPE html>
<html lang="en">
<head>
<meta charset="utf-8">
<title>Heron Loan Partners Business Card</title>
<link href="https://fonts.googleapis.com/css2?family=Poppins:wght@400;500;600&display=swap" rel="stylesheet">
<style>
  :root {
    --navy: #261f52;
    --gold: #dfb03c;
    --paper: #ffffff;
    --backdrop: #ababab;
    --rule: #a8a8ad;
  }
  html, body {
    margin: 0;
    padding: 0;
    width: 1093px;
    height: 1200px;
    overflow: hidden;
    background: var(--backdrop);
    font-family: "Poppins", sans-serif;
  }
  .card {
    position: absolute;
    left: 265px;
    width: 578px;
    height: 356px;
    border-radius: 24px;
    overflow: hidden;
  }
  .card--front { top: 226px; background: var(--paper); }
  .card--back { top: 621px; background: var(--navy); }

  .brand-name {
    position: absolute;
    margin: 0;
    font-weight: 600;
    color: var(--gold);
    white-space: nowrap;
    letter-spacing: 0.5px;
  }
  .card--front .brand-name {
    left: 40px;
    top: 160px;
    font-size: 27px;
    line-height: 36px;
  }
  .card--back .brand-name {
    left: 0;
    right: 0;
    top: 152px;
    text-align: center;
    font-size: 44px;
    line-height: 52px;
  }

  .divider {
    position: absolute;
    left: 288px;
    top: 75px;
    width: 1px;
    height: 208px;
    background: linear-gradient(to bottom, transparent, var(--rule) 15%, var(--rule) 85%, transparent);
  }

  .details {
    position: absolute;
    left: 311px;
    top: 88px;
    color: var(--navy);
  }
  .person-name {
    margin: 0;
    font-size: 24px;
    font-weight: 500;
    line-height: 28px;
    color: var(--gold);
  }
  .person-role {
    margin: 0;
    font-size: 17px;
    line-height: 20px;
  }
  .contact-list {
    list-style: none;
    margin: 16px 0 0;
    padding: 0;
  }
  .contact-item {
    display: flex;
    align-items: center;
    gap: 7px;
    font-size: 17.5px;
    line-height: 21px;
  }
  .contact-icon { width: 15px; height: 15px; flex: none; }
  .accent { color: var(--gold); }
  .address {
    margin: 14px 0 0;
    font-style: normal;
    font-size: 17px;
    line-height: 21px;
  }
</style>
</head>
<body>
  <section class="card card--front">
    <p class="brand-name">Heron Mortgage</p>
    <div class="divider"></div>
    <div class="details">
      <h1 class="person-name">Daniel Archer</h1>
      <p class="person-role">Managing Director</p>
      <ul class="contact-list">
        <li class="contact-item">
          <svg class="contact-icon" viewBox="0 0 16 16" aria-hidden="true">
            <path d="M4 1.5 6 5 4.6 6.4a9 9 0 0 0 5 5L11 10l3.5 2-1 2.4C8 15 1 8 1.6 2.5Z" fill="none" stroke="var(--gold)" stroke-width="1.5" stroke-linejoin="round"/>
            <path d="M9 2a5 5 0 0 1 5 5M9 4.5A2.5 2.5 0 0 1 11.5 7" fill="none" stroke="var(--gold)" stroke-width="1.3"/>
          </svg>
          055-318 742 260
        </li>
        <li class="contact-item">
          <svg class="contact-icon" viewBox="0 0 16 16" aria-hidden="true">
            <rect x="0.5" y="3" width="15" height="10" fill="var(--gold)"/>
            <path d="M0.5 3 8 9l7.5-6M0.5 13 6 7.5M15.5 13 10 7.5" fill="none" stroke="#fff" stroke-width="1"/>
          </svg>
          hello@heronloan.com
        </li>
        <li class="contact-item">
          <svg class="contact-icon" viewBox="0 0 16 16" aria-hidden="true">
            <g fill="none" stroke="var(--gold)" stroke-width="1.2">
              <circle cx="8" cy="8" r="7"/>
              <ellipse cx="8" cy="8" rx="3" ry="7"/>
              <path d="M1 8h14M2 4.5h12M2 11.5h12"/>
            </g>
          </svg>
          <span>www.<span class="accent">heronloan</span>.com</span>
        </li>
      </ul>
      <address class="address">87, Harbour View Road suite<br>30418,Eastbrook Bay</address>
    </div>
  </section>

  <section class="card card--back">
    <p class="brand-name">Heron Mortgage</p>
  </section>
</body>
</html>
```